Velk Partners Building Business Cards

We need a business card that reflects our business as "Solar Experts" in San Diego. Browse our website www.velkpartners.example our License needs to be displayed as "CSLB# 3867140" our phone number is (619) 555-0187

Save thousands on your electric bills and increase the value of your home while helping to protect the environment. Our solar installation experts will help you design the system that's right for you, using only the highest quality equipment that will look great and give you ideal performance. Our goal is to make you energy independent, and get your electric bill to 0.

Paul Osterby
(619) 555-0187
paul@velkpartners.example

Target Market(s)

Home owners in san diego looking for solar

Industry/Entity Type

Solar Energy

Contact Information for Business Card

Paul Osterby
(619) 555-0187
paul@velkpartners.example

Font styles to use
Other font styles liked:
• Use our logo font

Requirements
Must have
• License needs to be displayed as "CSLB# 3867140" our phone number is (619) 555-0187
Nice to have
• Real images of rooftop home solar in san diego
Should not have
• our business address

```html
<!DOCTYPE html>
<html lang="en">
<head>
<meta charset="utf-8">
<title>Velk Partners Building – Business Card</title>
<link rel="stylesheet" href="https://fonts.googleapis.com/css2?family=Open+Sans:wght@400;600;700&display=swap">
<style>
  :root {
    --page-bg: #d9d6d1;
    --card-bg: #eef0f1;
    --navy: #1c2a4f;
    --navy-deep: #0f1935;
    --orange: #e07b17;
    --orange-light: #f0a15a;
    --text-light: #e6e8ee;
    --text-muted: #c3c8d4;
  }
  * { box-sizing: border-box; margin: 0; padding: 0; }
  html, body {
    width: 1200px;
    height: 969px;
    overflow: hidden;
    background: var(--page-bg);
    font-family: "Open Sans", Arial, sans-serif;
  }
  .card {
    position: absolute;
    left: 382px;
    top: 106px;
    width: 436px;
    height: 757px;
    background: var(--card-bg);
    box-shadow: 0 10px 30px rgba(0,0,0,0.18);
    overflow: hidden;
  }
  .card-shape {
    position: absolute;
    left: 0;
    top: 0;
    width: 436px;
    height: 757px;
  }
  .brand-name {
    position: absolute;
    top: 128px;
    left: 0;
    width: 100%;
    text-align: center;
    font-size: 33px;
    font-weight: 700;
    color: var(--navy);
    letter-spacing: -0.3px;
  }
  .contact {
    position: absolute;
    left: 0;
    top: 362px;
    width: 100%;
    text-align: center;
  }
  .icon {
    display: block;
    margin: 0 auto;
    fill: var(--orange);
  }
  .person-name {
    margin-top: 4px;
    font-size: 28px;
    font-weight: 700;
    color: var(--orange);
    letter-spacing: 0.3px;
  }
  .person-title {
    margin-top: 2px;
    font-size: 21px;
    color: var(--text-light);
  }
  .contact-item {
    margin-top: 16px;
  }
  .contact-item .icon { margin-bottom: 4px; }
  .contact-text {
    font-size: 21px;
    color: var(--text-muted);
  }
  .contact-text.phone { color: var(--orange-light); }
  .licence {
    margin-top: 30px;
    font-size: 20px;
    color: var(--text-muted);
    letter-spacing: 0.5px;
  }
</style>
</head>
<body>
  <div class="card">
    <svg class="card-shape" viewBox="0 0 436 757" aria-hidden="true">
      <defs>
        <linearGradient id="panelFill" x1="0" y1="0" x2="0" y2="1">
          <stop offset="0" stop-color="#26365f"/>
          <stop offset="1" stop-color="#0e1833"/>
        </linearGradient>
      </defs>
      <polyline points="14,424 218,293 422,424" fill="none" stroke="#e07b17" stroke-width="7" stroke-linejoin="miter"/>
      <polygon points="0,432 218,308 436,432 436,757 0,757" fill="url(#panelFill)"/>
    </svg>

    <div class="brand-name">Velk Partners Building</div>

    <div class="contact">
      <svg class="icon" width="26" height="28" viewBox="0 0 26 28" aria-hidden="true">
        <circle cx="13" cy="8" r="7"/>
        <path d="M0 28 C0 19 5 16 13 16 C21 16 26 19 26 28 Z"/>
      </svg>
      <div class="person-name">Paul Osterby</div>
      <div class="person-title">CEO/Founder</div>

      <div class="contact-item">
        <svg class="icon" width="18" height="18" viewBox="0 0 24 24" aria-hidden="true">
          <path d="M6.6 10.8c1.4 2.8 3.8 5.1 6.6 6.6l2.2-2.2c.3-.3.7-.4 1-.2 1.1.4 2.3.6 3.6.6.6 0 1 .4 1 1V20c0 .6-.4 1-1 1C10.6 21 3 13.4 3 4c0-.6.4-1 1-1h3.5c.6 0 1 .4 1 1 0 1.3.2 2.5.6 3.6.1.3 0 .7-.2 1l-2.3 2.2z"/>
        </svg>
        <div class="contact-text phone">(619) 555-0187</div>
      </div>

      <div class="contact-item">
        <svg class="icon" width="18" height="14" viewBox="0 0 18 14" aria-hidden="true">
          <path d="M0 0h18v2L9 7.5 0 2z"/>
          <path d="M0 4l9 5.5L18 4v10H0z"/>
        </svg>
        <div class="contact-text">paul@velkpartners.example</div>
      </div>

      <div class="contact-item">
        <svg class="icon" width="18" height="18" viewBox="0 0 18 18" aria-hidden="true">
          <circle cx="9" cy="9" r="9"/>
          <path d="M9 0v18M0 9h18M3 3.5c3.5 2 8.5 2 12 0M3 14.5c3.5-2 8.5-2 12 0" stroke="#1c2a4f" stroke-width="1.2" fill="none"/>
        </svg>
        <div class="contact-text">www.velkpartners.example</div>
      </div>

      <div class="licence">CSLB# 3867140</div>
    </div>
  </div>
</body>
</html>
```